Modern Attractive Letterhead for Veterinary House Call Business.

A letterhead which can be printed on A4, A5 and A6 paper sizes.
To have: ( our files to be uploaded)
1. Logo with Text
2. telephone
3. email
4. website
5. Address

Target Market(s)

60-85year mainly women pet owners. Also market include families, young professionals, busy people who have dogs and cats

Industry/Entity Type

Business

Requirements
Must have
• 1. Logo with Text ( provided)
• 2. telephone
• 3. email
• 4. website
• 5. Address
Nice to have
• Needs to be modern, preferably warm and caring in nature( if possible )
Should not have
• difficulty in printing A5 and A6

```html
<!DOCTYPE html>
<html lang="en">
<head>
<meta charset="utf-8">
<title>Larkfield Pet Clinic — Letterhead</title>
<link href="https://fonts.googleapis.com/css2?family=Cinzel:wght@400;600&display=swap" rel="stylesheet">
<style>
  :root {
    --blue-deep: #1f3fb0;
    --blue-light: #4fc6f2;
    --green: #5cb82a;
    --ink: #3a3a3a;
    --paper: #ffffff;
    --page-bg: #ececec;
    --rule: #2b55c4;
  }
  html, body {
    margin: 0;
    padding: 0;
    width: 919px;
    height: 1200px;
    overflow: hidden;
    background: var(--page-bg);
  }
  .letterhead {
    position: relative;
    width: 919px;
    height: 1200px;
    background: var(--paper);
    font-family: "Cinzel", serif;
    overflow: hidden;
  }
  .header-swoosh {
    position: absolute;
    left: 0;
    top: 0;
    width: 919px;
    height: 330px;
  }
  .brand {
    position: absolute;
    left: 30px;
    top: 80px;
    display: flex;
    align-items: center;
    gap: 16px;
  }
  .brand-mark {
    width: 30px;
    height: 30px;
    border-radius: 50%;
    background: var(--blue-deep);
  }
  .brand-name {
    margin: 0;
    font-family: "Cinzel", serif;
    font-weight: 400;
    font-size: 30px;
    color: var(--ink);
    letter-spacing: 1px;
  }
  .address {
    position: absolute;
    right: 56px;
    top: 44px;
    margin: 0;
    text-align: right;
    font-style: normal;
    font-weight: 600;
    font-size: 20px;
    line-height: 25px;
    color: var(--paper);
    letter-spacing: 0.5px;
  }
  .emblem-watermark {
    position: absolute;
    left: 262px;
    top: 548px;
    width: 360px;
    height: 530px;
    border-radius: 48% 48% 40% 40%;
    background: radial-gradient(ellipse at 50% 40%, rgba(205,214,238,0.45), rgba(228,234,246,0.2) 60%, rgba(255,255,255,0) 78%);
  }
  .footer-rule {
    position: absolute;
    left: 96px;
    top: 1127px;
    width: 746px;
    height: 2px;
    background: linear-gradient(90deg, rgba(43,85,196,0), var(--rule) 12%, var(--rule) 88%, rgba(43,85,196,0));
  }
  .contact {
    position: absolute;
    top: 1148px;
    left: 0;
    right: 0;
    margin: 0;
    padding: 0;
    list-style: none;
    font-size: 16px;
    color: var(--ink);
  }
  .contact-item {
    position: absolute;
    display: flex;
    align-items: center;
    gap: 8px;
    white-space: nowrap;
  }
  .contact-item svg { flex: none; }
  .contact-phone { left: 74px; font-family: Georgia, "Times New Roman", serif; }
  .contact-email { left: 222px; }
  .contact-web { left: 550px; }
</style>
</head>
<body>
<main class="letterhead">
  <svg class="header-swoosh" viewBox="0 0 919 330" aria-hidden="true">
    <defs>
      <linearGradient id="band-blue" x1="0" y1="0" x2="1" y2="0">
        <stop offset="0" stop-color="#4fc6f2"/>
        <stop offset="0.45" stop-color="#3aa5e8"/>
        <stop offset="1" stop-color="#1f3fb0"/>
      </linearGradient>
    </defs>
    <path d="M0,0 H919 V306 C860,112 560,26 0,8 Z" fill="var(--green)"/>
    <path d="M0,0 H919 V264 C855,108 560,20 0,5 Z" fill="var(--paper)"/>
    <path d="M0,0 H919 V252 C855,102 560,16 0,3 Z" fill="url(#band-blue)"/>
  </svg>

  <div class="brand">
    <span class="brand-mark"></span>
    <h1 class="brand-name">Larkfield Pet Clinic</h1>
  </div>

  <address class="address">
    Po Box 5521<br>
    Wattlebrook<br>
    Qld 4120
  </address>

  <div class="emblem-watermark" role="img" aria-label="Faint brand emblem watermark"></div>

  <div class="footer-rule"></div>

  <ul class="contact">
    <li class="contact-item contact-phone">
      <svg width="18" height="18" viewBox="0 0 18 18" aria-hidden="true">
        <circle cx="9" cy="9" r="8" fill="none" stroke="var(--green)" stroke-width="1.6"/>
        <path d="M6.2,4.8 l1.6,1.6 -0.9,1.1 c0.5,1.2 1.4,2.1 2.6,2.6 l1.1,-0.9 1.6,1.6 -1.2,1.3 c-2.9,-0.5 -5.2,-2.8 -5.7,-5.7 z" fill="var(--green)"/>
      </svg>
      0491570110
    </li>
    <li class="contact-item contact-email">
      <svg width="20" height="14" viewBox="0 0 20 14" aria-hidden="true">
        <rect x="0" y="0" width="20" height="14" rx="1" fill="var(--green)"/>
        <path d="M1,1 L10,8 L19,1" fill="none" stroke="#ffffff" stroke-width="1.4"/>
      </svg>
      info@larkfieldclinic.com.au
    </li>
    <li class="contact-item contact-web">
      <svg width="20" height="20" viewBox="0 0 20 20" aria-hidden="true">
        <g fill="none" stroke="var(--green)" stroke-width="1.4">
          <circle cx="10" cy="10" r="8.5"/>
          <ellipse cx="10" cy="10" rx="4" ry="8.5"/>
          <line x1="1.5" y1="10" x2="18.5" y2="10"/>
          <path d="M3,5.5 H17 M3,14.5 H17"/>
        </g>
      </svg>
      www.larkfieldclinic.com.au
    </li>
  </ul>
</main>
</body>
</html>
```